Buch-/eBook-Cover für ein Fantasy Roman
Zielgruppe
Meine Zielgruppe sind Jugendliche und junge Erwachsene, aber auch für Ältere könnte mein Buch interessant sein.
Aufgabenstellung
Bei meinem Buch handelt es sich um einen Fantasy Roman. Es heißt 'Drifter - Wo die Stille wohnt' und der Autor ist Mara Wendholt.
Das Buch handelt von einem Mädchen, welches eigentlich ein ganz normales Leben führt, aber dieses durch eine Pressekonferenz vom Präsidenten komplett durcheinander gerät. Denn viele Menschen sollen an einem Virus leiden. Die Menschen sollen sich aber keine Sorgen machen. Doch alles läuft durcheinander, da die infizierten Menschen einer nach dem anderen spurlos verschwinden.
Auf meinem Cover soll keine Figur zu sehen sein. Ich hätte gerne ein Zusammenspiel zwischen den Farben Blau und Grün. sie sollen harmonisch und fließend ineinander übergehen. Auch etwas Glitzer für etwas Geheimnisvolles darf auf dem Cover sein. Den Titel hätte ich gerne in der Mitte. Wo der Autorname stehen soll, bin ich offen.

```html
<!DOCTYPE html>
<html lang="de">
<head>
<meta charset="utf-8">
<title>Drifter – Wo die Stille wohnt · Buchumschlag</title>
<link rel="stylesheet" href="https://fonts.googleapis.com/css2?family=Cinzel:wght@400;600&family=EB+Garamond:wght@400&display=swap">
<style>
  :root{
    --ink-deep:#03121a;
    --ink-navy:#0a2a44;
    --ink-teal:#1b8a8c;
    --ink-aqua:#3fb5b0;
    --ink-green:#1f6a5a;
    --paper:#ffffff;
    --text-light:#f4f1ea;
    --gold-light:#f7dfb0;
    --gold-mid:#c99a5c;
    --gold-dark:#7a5430;
  }
  *{margin:0;padding:0;box-sizing:border-box;}
  html,body{width:1200px;height:888px;overflow:hidden;background:var(--ink-deep);}
  .cover-wrap{position:relative;width:1200px;height:888px;overflow:hidden;}

  .artwork{
    position:absolute;inset:0;
    background:
      radial-gradient(ellipse 260px 200px at 80px 80px, rgba(63,181,176,.55), transparent 70%),
      radial-gradient(ellipse 300px 220px at 1130px 120px, rgba(63,181,176,.45), transparent 70%),
      radial-gradient(ellipse 260px 300px at 260px 640px, rgba(63,181,176,.55), transparent 70%),
      radial-gradient(ellipse 260px 300px at 940px 640px, rgba(63,181,176,.5), transparent 70%),
      radial-gradient(ellipse 200px 240px at 470px 820px, rgba(31,106,90,.6), transparent 70%),
      radial-gradient(ellipse 200px 240px at 730px 820px, rgba(31,106,90,.6), transparent 70%),
      radial-gradient(ellipse 160px 300px at 600px 420px, rgba(3,18,26,.9), transparent 75%),
      linear-gradient(180deg, var(--ink-navy) 0%, #0c3a4e 45%, #0b3340 75%, #0a2b33 100%);
  }

  .gold{
    background:linear-gradient(180deg,var(--gold-light) 0%,var(--gold-mid) 45%,var(--gold-dark) 60%,var(--gold-light) 100%);
    -webkit-background-clip:text;background-clip:text;color:transparent;
  }

  /* Rückseite */
  .back-blurb{
    position:absolute;left:63px;top:78px;width:433px;
    font-family:"EB Garamond",serif;font-size:19.4px;line-height:25.4px;
    color:var(--text-light);text-align:justify;
  }
  .barcode-field{
    position:absolute;left:344px;top:729px;width:201px;height:119px;background:var(--paper);
  }

  /* Buchrücken */
  .spine{
    position:absolute;left:575px;top:0;width:50px;height:888px;
  }
  .spine-text{
    position:absolute;left:50%;transform:translateX(-50%);
    writing-mode:vertical-rl;white-space:nowrap;
  }
  .spine-title{top:72px;font-family:"Cinzel",serif;font-size:40px;font-weight:400;line-height:1;}
  .spine-subtitle{top:285px;font-family:"EB Garamond",serif;font-size:15.5px;color:var(--text-light);line-height:1;}
  .spine-author{top:575px;font-family:"Cinzel",serif;font-size:22px;line-height:1;letter-spacing:.5px;}

  /* Vorderseite */
  .front-title{
    position:absolute;left:660px;top:325px;width:515px;text-align:center;
    font-family:"Cinzel",serif;font-weight:600;font-size:112px;line-height:1;
    filter:drop-shadow(0 2px 3px rgba(0,0,0,.55));
  }
  .front-subtitle{
    position:absolute;left:660px;top:484px;width:515px;text-align:center;
    font-family:"EB Garamond",serif;font-size:30px;line-height:1;color:var(--text-light);
  }
  .front-author{
    position:absolute;left:660px;top:808px;width:515px;text-align:center;
    font-family:"Cinzel",serif;font-size:29px;line-height:1;letter-spacing:1px;
  }
</style>
</head>
<body>
<main class="cover-wrap">
  <div class="artwork" role="img" aria-label="Fließende Tinten- und Rauchschwaden in Blau und Türkis mit goldenem Glitzer, spiegelsymmetrisch über den gesamten Umschlag"></div>

  <section class="back-cover">
    <p class="back-blurb">Lorem ipsum dolor sit amet, consetetur sadipscing elitr, sed diam nonumy eirmod tempor invidunt ut labore et dolore magna aliquyam erat, sed diam voluptua. At vero eos et accusam et justo duo dolores et ea rebum. Stet clita kasd gubergren, no sea takimata sanctus est Lorem ipsum dolor sit amet. Lorem ipsum dolor sit amet, consetetur sadipscing elitr, sed diam nonumy eirmod tempor invidunt ut labore et dolore magna aliquyam erat, sed diam voluptua. At vero eos et accusam et justo duo dolores et ea rebum. Stet clita kasd gubergren, no sea takimata sanctus est Lorem ipsum dolor sit amet.</p>
    <div class="barcode-field"></div>
  </section>

  <section class="spine">
    <h2 class="spine-text spine-title gold">DRIFTER</h2>
    <p class="spine-text spine-subtitle">WO DIE STILLE WOHNT</p>
    <p class="spine-text spine-author gold">MARA WENDHOLT</p>
  </section>

  <section class="front-cover">
    <h1 class="front-title gold">DRIFTER</h1>
    <p class="front-subtitle">WO DIE STILLE WOHNT</p>
    <p class="front-author gold">MARA WENDHOLT</p>
  </section>
</main>
</body>
</html>
```